Professional violinist needs business cards

I am trying to attract the following jobs:
-private violin lessons (primarily classical)
-performance gigs (weddings, birthday parties, funerals, etc.)
-collaborations with other artists (studio recordings, performances)

I want to communicate that I have a very high standard of excellence for my work, but I also love people and celebrations.
Values/style words I like are:
love, joy, peace, fun, beauty, authenticity, excellence, warmth, refined/sleek, free spirited. If that's too confusing, just ignore :)

I will attach my favorite business card template that I could find on Canva. The lines are supposed to be like a music staff, which I think is really cool, but I also don't want it to look too busy. I like the simple black and white--I think it looks sharp--but I also am open to other ideas. I also have seen business cards with pictures included that looked great, so I attached an image that could be used as well.

I am also attaching a file that I made of my initials that could be used as a logo, but I'm not sure if it should be included.

Information on the card:
-My name (18 letters total)
-"violinist"
-phone number, email, website

Thank you!

```html
<!DOCTYPE html>
<html lang="en">
<head>
<meta charset="utf-8">
<title>Marisol Everhartly — Violinist Business Card</title>
<link rel="stylesheet" href="https://fonts.googleapis.com/css2?family=Barlow+Condensed:wght@300;500;700&family=Barlow+Semi+Condensed:wght@500&display=swap">
<style>
  :root {
    --backdrop: #8a8c90;
    --card-white: #ffffff;
    --card-black: #050507;
    --ink-black: #050507;
    --ink-white: #ffffff;
  }
  html, body {
    margin: 0;
    padding: 0;
    width: 1200px;
    height: 1200px;
    overflow: hidden;
    background: var(--backdrop);
  }
  .stage {
    position: relative;
    width: 1200px;
    height: 1200px;
  }
  .card {
    position: absolute;
    left: 220px;
    width: 760px;
    height: 434px;
    box-shadow: 0 6px 18px rgba(0,0,0,0.25);
  }
  .card--front {
    top: 120px;
    background: var(--card-white);
  }
  .card--back {
    top: 646px;
    background: var(--card-black);
  }

  /* Front: plain emblem circle with the name set beside it */
  .emblem {
    position: absolute;
    left: 120px;
    top: 92px;
    width: 250px;
    height: 250px;
  }
  .front-name {
    position: absolute;
    left: 400px;
    top: 192px;
    margin: 0;
    font-family: "Barlow Condensed", sans-serif;
    font-weight: 500;
    font-size: 36px;
    line-height: 1;
    letter-spacing: 0.04em;
    text-transform: uppercase;
    color: var(--ink-black);
  }

  /* Back: contact block */
  .details {
    position: absolute;
    left: 330px;
    top: 78px;
    color: var(--ink-white);
  }
  .details__name {
    margin: 0;
    font-family: "Barlow Condensed", sans-serif;
    font-size: 46px;
    line-height: 1;
    text-transform: uppercase;
    letter-spacing: 0.01em;
  }
  .details__first { font-weight: 700; }
  .details__last { font-weight: 300; }
  .details__role {
    margin: 14px 0 0;
    font-family: "Barlow Condensed", sans-serif;
    font-weight: 300;
    font-size: 24px;
    letter-spacing: 0.45em;
    text-transform: uppercase;
  }
  .details__contact {
    list-style: none;
    margin: 44px 0 0;
    padding: 0;
    font-family: "Barlow Semi Condensed", sans-serif;
    font-weight: 500;
    font-size: 28px;
    line-height: 1;
  }
  .details__contact li + li { margin-top: 24px; }
</style>
</head>
<body>
  <main class="stage">
    <section class="card card--front" aria-label="Card front">
      <svg class="emblem" viewBox="0 0 250 250" aria-hidden="true">
        <circle cx="125" cy="125" r="125" fill="var(--ink-black)"/>
      </svg>
      <p class="front-name">Marisol Everhartly</p>
    </section>

    <section class="card card--back" aria-label="Card back">
      <div class="details">
        <h1 class="details__name"><span class="details__first">Marisol</span> <span class="details__last">Everhartly</span></h1>
        <p class="details__role">Violinist</p>
        <ul class="details__contact">
          <li>+00 4821 306 775</li>
          <li>marisoleverhartly@mailbox.com</li>
          <li>www.marisolstrings.com</li>
        </ul>
      </div>
    </section>
  </main>
</body>
</html>
```